Website Design for a holiday home letting busines

We require a redesign of our present website www.pinebrookstays.com. We want the website to stand out and look professional and clean to make holiday hunters want to book a caravan or lodge holiday with us. Our logo is red however we DO NOT want the website to be red. We want a natural colour scheme.

The final design should communicate that we are a professional company to book with.

On the home page we require;
Overview of company
Photo
Search box for holiday (check in)
Late Deals
Reviews
News

We would like the following pages designed; home page, available dates page, caravans page, content page.

The website should be responsive for smart phones. One website I do like is http://www.verdoliso.be/nl/

Target Market(s)

Families

Industry/Entity Type

Travel

Number of Pages Required

5+ page

Font styles to use
Serif

Requirements
Must have
• The project must be responsive for mobile phones and tablets.
• Ability to search for holiday home holidays
• We want a natural colour scheme.
Nice to have
• A style we like is http://www.verdoliso.be/nl/
Should not have
• Do not use red as a colour for the website. Our logo is red so this is the only time we want this used.

```html
<!DOCTYPE html>
<html lang="en">
<head>
<meta charset="utf-8">
<title>Pinebrook Stays – Private Holiday Rentals</title>
<link href="https://fonts.googleapis.com/css2?family=PT+Sans:wght@400;700&family=Open+Sans:wght@400;600;700&display=swap" rel="stylesheet">
<style>
:root{
  --blue:#1f7ac4;
  --blue-dark:#16609c;
  --green:#8bbf3c;
  --green-dark:#74a72b;
  --ink:#333a40;
  --muted:#7b838a;
  --light:#f0f1f2;
  --line:#dcdfe2;
  --white:#ffffff;
  --logo:#c9262c;
  --star:#f0a81e;
}
*{box-sizing:border-box;margin:0;padding:0}
html,body{width:1200px;height:3788px;overflow:hidden}
body{font-family:"Open Sans",Arial,sans-serif;color:var(--ink);background:var(--white);position:relative;font-size:13px}
h1,h2,h3,h4,.nav,.btn{font-family:"PT Sans",Arial,sans-serif}
.abs{position:absolute}

/* header */
.topbar{position:absolute;left:0;top:0;width:1200px;height:150px;background:var(--white)}
.brand{position:absolute;left:100px;top:28px;display:flex;align-items:center;gap:12px}
.brand-dot{width:44px;height:44px;border-radius:50%;background:var(--logo)}
.brand-name{font-family:"PT Sans",sans-serif;font-weight:700;font-size:28px;color:var(--ink)}
.brand-tag{position:absolute;left:156px;top:76px;font-size:11px;color:var(--muted)}
.season{position:absolute;top:12px;height:30px;border-radius:15px;color:#fff;font:700 14px "PT Sans",sans-serif;display:flex;align-items:center;justify-content:center;width:150px}
.season.past{left:790px;background:#8d9296}
.season.next{left:950px;background:var(--blue)}
.phones{position:absolute;top:62px;left:790px;display:flex;gap:28px}
.phones div{font-size:10px;color:var(--muted);line-height:1.3}
.phones b{display:block;font:700 16px "PT Sans",sans-serif;color:var(--ink)}
.nav{position:absolute;left:0;top:150px;width:1200px;height:42px;background:var(--light);border-top:1px solid var(--line);border-bottom:1px solid var(--line)}
.nav ul{list-style:none;display:flex;margin-left:100px;height:100%}
.nav li{padding:0 17px;display:flex;align-items:center;font-size:13px;font-weight:700;color:#555;text-transform:uppercase}
.nav li.active{background:var(--blue);color:#fff}

/* hero */
.hero{position:absolute;left:0;top:192px;width:1200px;height:630px;background:linear-gradient(180deg,#8fc2e8 0%,#b9d8ee 38%,#5f8fae 52%,#7c7f72 70%,#4f5449 100%)}
.hero-copy{position:absolute;left:100px;top:180px}
.hero-copy .l1{font:700 40px "PT Sans",sans-serif;color:#fff;letter-spacing:1px}
.hero-copy .l2{display:inline-block;background:#fff;color:var(--blue);font:700 40px "PT Sans",sans-serif;padding:0 12px;margin-top:4px}
.hero-copy .l3{width:330px;margin-top:12px;background:var(--blue);color:#fff;font-size:12px;font-weight:600;padding:10px 14px;line-height:1.5}
.arrow{position:absolute;top:300px;width:36px;height:36px;border-radius:50%;background:rgba(255,255,255,.3);display:flex;align-items:center;justify-content:center}
.checkin{position:absolute;left:620px;top:60px;width:480px;height:360px;background:rgba(255,255,255,.82);padding:24px 30px}
.checkin h2{font-size:30px;color:var(--ink);font-weight:700;border-bottom:1px solid var(--line);padding-bottom:12px;margin-bottom:18px}
.field{height:40px;background:#fff;border:1px solid var(--line);border-radius:4px;font-size:12px;color:var(--muted);display:flex;align-items:center;justify-content:space-between;padding:0 14px;margin-bottom:14px}
.field-row{display:flex;gap:14px}
.field-row .field{flex:1}
.search-btn{height:42px;background:var(--blue);color:#fff;border-radius:4px;font:700 15px "PT Sans",sans-serif;display:flex;align-items:center;justify-content:center}

/* intro band */
.intro{position:absolute;left:0;top:822px;width:1200px;height:420px;background:var(--light)}
.slider{position:absolute;left:100px;top:22px;width:490px;height:370px;background:linear-gradient(135deg,#3e4a52,#1f272d)}
.slider h3{position:absolute;left:40px;top:70px;font-size:22px;color:#fff}
.slider h3 span{color:var(--green)}
.slider p{position:absolute;left:40px;top:112px;width:400px;font-size:11px;line-height:1.6;color:#dde2e5}
.dots{display:flex;gap:8px}
.dots i{width:8px;height:8px;border-radius:50%;background:#bbb;display:block}
.dots i.on{background:var(--blue)}
.welcome{position:absolute;left:612px;top:22px;width:488px;height:170px;background:var(--green);color:#fff;padding:44px 34px}
.welcome h2{font-size:30px;line-height:1.2;font-weight:700}
.reviews{position:absolute;left:612px;top:212px;width:488px;height:180px;background:var(--green-dark);color:#fff;padding:28px 40px}
.reviews h2{font-size:30px;font-weight:700;margin-bottom:10px}
.reviews p{font-size:11px;line-height:1.6}

/* section titles */
.sec-title{position:absolute;left:0;width:1200px;text-align:center;font:700 30px "PT Sans",sans-serif;color:var(--ink);text-transform:uppercase}
.sec-title::after{content:"";display:block;width:1000px;height:1px;background:var(--line);margin:14px auto 0}

/* lodges grid */
.grid{position:absolute;left:100px;top:1380px;width:1000px;height:460px;display:grid;grid-template-columns:repeat(4,250px);grid-template-rows:230px 230px;border:1px solid var(--line)}
.cell-photo{background:linear-gradient(135deg,#b99c7c,#6e5744)}
.cell-text{background:#fff;padding:24px 20px;position:relative}
.cell-text h4{font-size:20px;font-weight:700;margin-bottom:10px;text-transform:uppercase}
.cell-text p{font-size:11px;color:var(--muted);line-height:1.6}
.more{position:absolute;left:20px;bottom:24px;background:var(--green);color:#fff;font-size:10px;font-weight:600;padding:5px 10px;border-radius:2px}
.stars{position:absolute;right:20px;bottom:26px;color:var(--star);font-size:12px;letter-spacing:1px}
.view-all{position:absolute;left:100px;top:1880px;width:1000px;height:44px}
.view-all::before{content:"";position:absolute;left:0;right:0;top:22px;height:1px;background:var(--line)}
.view-all span{position:absolute;left:420px;width:160px;height:44px;border-radius:22px;background:var(--blue);color:#fff;font:700 15px "PT Sans",sans-serif;display:flex;align-items:center;justify-content:center}

/* late deals */
.deals{position:absolute;left:0;top:1964px;width:1200px;height:410px;background:linear-gradient(180deg,#4a5157,#2b3136)}
.deals .sec-title{color:#fff;top:36px}
.deals .sec-title::after{display:none}
.deal{position:absolute;top:100px;width:490px;height:260px;background:#fff;display:flex}
.deal .img{width:250px;height:260px}
.deal .txt{position:relative;flex:1;padding:26px 20px}
.deal h4{font-size:20px;font-weight:700;margin-bottom:10px}
.deal p{font-size:11px;color:var(--muted);line-height:1.6}

/* newsletter & news */
.newsletter{position:absolute;left:100px;top:2420px;width:640px;height:350px;background:linear-gradient(160deg,#cfdfe9,#6e8a5b)}
.newsletter h3{position:absolute;left:0;top:24px;background:var(--blue);color:#fff;font-size:26px;font-weight:700;padding:8px 30px;width:420px}
.nl-input{position:absolute;left:30px;width:300px;height:40px;background:#fff;border:1px solid var(--line);font-size:12px;color:var(--muted);display:flex;align-items:center;padding:0 14px}
.nl-btn{position:absolute;left:30px;top:220px;width:110px;height:38px;background:var(--blue-dark);color:#fff;font:700 13px "PT Sans",sans-serif;display:flex;align-items:center;justify-content:center}
.news{position:absolute;left:780px;top:2420px;width:320px}
.news h3{font-size:30px;font-weight:700;border-bottom:1px solid var(--line);padding-bottom:10px;margin-bottom:18px}
.news-item{display:flex;gap:14px;margin-bottom:26px}
.news-item .thumb{width:100px;height:76px;flex:none;background:linear-gradient(135deg,#9fb98a,#5f7d4a)}
.news-item h5{font:700 13px "PT Sans",sans-serif;margin-bottom:5px}
.news-item p{font-size:10px;color:var(--muted);line-height:1.5}

/* amenities */
.amenities{position:absolute;left:100px;top:2945px;width:1000px;display:grid;grid-template-columns:repeat(3,1fr);gap:0 30px}
.amenities ul{list-style:none}
.amenities li{font-size:13px;line-height:23px;color:#555;padding-left:18px;position:relative}
.amenities li::before{content:"";position:absolute;left:0;top:8px;width:7px;height:7px;background:var(--blue)}

/* footer */
.footer{position:absolute;left:0;top:3262px;width:1200px;height:478px;background:var(--blue)}
.fcol{position:absolute;top:44px;color:#fff}
.fcol h4{font-size:22px;font-weight:700;margin-bottom:14px;padding-bottom:10px;border-bottom:1px solid rgba(255,255,255,.35)}
.fcol p,.fcol li{font-size:11px;line-height:1.75;color:#e3eef8}
.fcol ul{list-style:none}
.fcol li::before{content:"› ";}
.f-input{height:28px;background:#fff;margin-bottom:8px;border-radius:2px;font-size:10px;color:var(--muted);padding:6px 10px}
.f-btn{display:inline-block;background:var(--blue-dark);color:#fff;font:700 12px "PT Sans",sans-serif;padding:7px 16px;border:1px solid #fff}
.copyright{position:absolute;left:0;top:3740px;width:1200px;height:48px;background:var(--blue-dark);color:#dfeaf4;font-size:11px;display:flex;align-items:center;padding-left:100px}
</style>
</head>
<body>

<header class="topbar">
  <div class="brand"><span class="brand-dot"></span><span class="brand-name">Pinebrook Stays</span></div>
  <div class="brand-tag">Lodge and caravan hire at Alder Bay</div>
  <div class="season past">2015 HOLIDAYS</div>
  <div class="season next">2016 HOLIDAYS</div>
  <div class="phones">
    <div>GENERAL ENQUIRY<b>0800 555 0142</b></div>
    <div>FOR BOOKINGS<b>0800 555 0143</b></div>
    <div>LINES OPEN<b>9AM</b></div>
  </div>
</header>
<nav class="nav">
  <ul>
    <li class="active">Home</li><li>News</li><li>Reviews</li><li>Caravans &amp; Lodges</li><li>Owners' Page</li><li>Park Facts</li><li>Local Attractions</li><li>Contact</li>
  </ul>
</nav>

<section class="hero" role="img" aria-label="Photo of a coastal road beside the sea under a bright sky">
  <div class="hero-copy">
    <div class="l1">PRIVATE</div>
    <div class="l2">HOLIDAY RENTALS</div>
    <div class="l3">QUALITY LODGE &amp; CARAVAN HIRE AT ALDER BAY HOLIDAY PARK. BOOK ONLINE TODAY!</div>
  </div>
  <div class="arrow" style="left:30px"><svg width="12" height="16"><path d="M9 2 L3 8 L9 14" stroke="#fff" stroke-width="2.5" fill="none"/></svg></div>
  <div class="arrow" style="right:30px"><svg width="12" height="16"><path d="M3 2 L9 8 L3 14" stroke="#fff" stroke-width="2.5" fill="none"/></svg></div>
  <form class="checkin">
    <h2>CHECK IN</h2>
    <div class="field">Where Are You Going?<svg width="14" height="14"><circle cx="6" cy="6" r="4.5" stroke="#999" stroke-width="1.6" fill="none"/><path d="M9.5 9.5 L13 13" stroke="#999" stroke-width="1.6"/></svg></div>
    <div class="field-row">
      <div class="field">Check In<svg width="14" height="14"><rect x="1" y="2" width="12" height="11" stroke="#999" fill="none"/><path d="M1 5 H13" stroke="#999"/></svg></div>
      <div class="field">Check Out<svg width="14" height="14"><rect x="1" y="2" width="12" height="11" stroke="#999" fill="none"/><path d="M1 5 H13" stroke="#999"/></svg></div>
    </div>
    <div class="field">Guests<svg width="12" height="8"><path d="M1 1 L6 6 L11 1" stroke="#999" stroke-width="1.6" fill="none"/></svg></div>
    <div class="search-btn">Search</div>
  </form>
</section>

<section class="intro">
  <div class="slider" role="img" aria-label="Slider photo of a lodge interior at dusk">
    <h3>CONTRARY TO <span>POPULAR BELIEF</span></h3>
    <p>Contrary to popular belief, our lodges are not simply places to sleep. Each one sits in a quiet corner of the park with room to relax, play and explore the coast, woodland walks and village cafés nearby.</p>
    <div class="dots" style="position:absolute;left:205px;bottom:28px"><i class="on"></i><i></i><i></i><i></i></div>
    <svg class="abs" style="left:16px;top:176px" width="12" height="18"><path d="M9 2 L3 9 L9 16" stroke="#fff" stroke-width="2.5" fill="none"/></svg>
    <svg class="abs" style="right:16px;top:176px" width="12" height="18"><path d="M3 2 L9 9 L3 16" stroke="#fff" stroke-width="2.5" fill="none"/></svg>
  </div>
  <div class="welcome"><h2>WELCOME TO PINEBROOK STAYS HOLIDAYS</h2></div>
  <div class="reviews">
    <h2>REVIEWS</h2>
    <p>Lovely clean lodge, friendly owners and a great park for the children. We will be back again next summer for another week by the sea.</p>
    <svg class="abs" style="left:14px;top:82px" width="10" height="16"><path d="M8 2 L2 8 L8 14" stroke="#fff" stroke-width="2.2" fill="none"/></svg>
    <svg class="abs" style="right:14px;top:82px" width="10" height="16"><path d="M2 2 L8 8 L2 14" stroke="#fff" stroke-width="2.2" fill="none"/></svg>
  </div>
</section>

<h2 class="sec-title" style="top:1300px">Our Caravans and Lodges</h2>
<section class="grid">
  <div class="cell-photo" role="img" aria-label="Photo of a caravan living room"></div>
  <div class="cell-text"><h4>The Larchwood</h4><p>A bright family caravan with open plan lounge, two bedrooms and a sunny deck.</p><span class="more">Read More</span><span class="stars">★★★★★</span></div>
  <div class="cell-photo" role="img" aria-label="Photo of a lodge lounge" style="background:linear-gradient(135deg,#c7b59a,#7b6a55)"></div>
  <div class="cell-text"><h4>The Heronmere</h4><p>A spacious lodge with modern kitchen, cosy lounge and views over the lake.</p><span class="more">Read More</span><span class="stars">★★★★★</span></div>
  <div class="cell-text"><h4>The Thistledown</h4><p>A comfortable caravan close to the pool, shop and children's play area.</p><span class="more">Read More</span><span class="stars">★★★★★</span></div>
  <div class="cell-photo" role="img" aria-label="Photo of a caravan bedroom" style="background:linear-gradient(135deg,#e4e0da,#a9a39a)"></div>
  <div class="cell-text"><h4>The Bramblewick</h4><p>A quiet lodge with private garden, sleeping six and ideal for longer stays.</p><span class="more">Read More</span><span class="stars">★★★★★</span></div>
  <div class="cell-photo" role="img" aria-label="Photo of a lodge kitchen and dining area" style="background:linear-gradient(135deg,#a79882,#5d5345)"></div>
</section>
<div class="view-all"><span>VIEW ALL</span></div>

<section class="deals" role="img" aria-label="Darkened photo of a holiday park at evening">
  <h2 class="sec-title">Late Deals</h2>
  <div class="deal" style="left:100px">
    <div class="img" role="img" aria-label="Photo of a caravan exterior on the park" style="background:linear-gradient(135deg,#9cc3e4,#6f9158)"></div>
    <div class="txt"><h4>THE LARCHWOOD</h4><p>Three nights from Friday with a late saving on our most popular family caravan.</p><span class="more">Read More</span><span class="stars">★★★★★</span></div>
  </div>
  <div class="deal" style="left:610px">
    <div class="img" role="img" aria-label="Photo of a family enjoying a lodge holiday" style="background:linear-gradient(135deg,#7fb2d8,#b78f6a)"></div>
    <div class="txt"><h4>THE HERONMERE</h4><p>Midweek break this month with free late checkout and a welcome pack on arrival.</p><span class="more">Read More</span><span class="stars">★★★★★</span></div>
  </div>
</section>

<section class="newsletter" role="img" aria-label="Photo of a lodge exterior with lawn">
  <h3>SIGNUP FOR NEWSLETTER</h3>
  <div class="nl-input" style="top:110px">Your Name</div>
  <div class="nl-input" style="top:164px">Your Email</div>
  <div class="nl-btn">SUBSCRIBE</div>
</section>
<section class="news">
  <h3>LATEST NEWS</h3>
  <div class="news-item"><div class="thumb" role="img" aria-label="Photo of the park in summer"></div><div><h5>NEW LODGES OPEN ON THE LAKE SIDE</h5><p>Four new lodges are ready for booking this season with decks facing the water.</p></div></div>
  <div class="news-item"><div class="thumb" role="img" aria-label="Photo of a caravan interior" style="background:linear-gradient(135deg,#d6c6ad,#8c7a62)"></div><div><h5>SUMMER EVENTS ON THE PARK</h5><p>Family discos, nature walks and craft mornings run every week until September.</p></div></div>
</section>

<h2 class="sec-title" style="top:2860px">What is at the Holiday Park ?</h2>
<section class="amenities">
  <ul><li>Amenities Blocks</li><li>Baby Bath</li><li>BBQ</li><li>Bike Club Local Benefits</li><li>Cafes</li><li>Camp Kitchen</li><li>Canoeing</li><li>Clothes Line</li><li>Convenience Store/Kiosk</li></ul>
  <ul><li>Daily &amp; High Chair Hire</li><li>Drive Through Sites</li><li>Ensuite Sites</li><li>Family Bathroom</li><li>Gas Swap Bottles or Refills</li><li>Go Karts (unpowered)</li><li>Groups Welcome</li><li>Inflatable Trampoline</li><li>Internet – Free Wireless</li></ul>
  <ul><li>Internet Kiosk</li><li>Kids Playground</li><li>Large – Pet Friendly Sites</li><li>Laundries with Washing Machines</li><li>Lending Library</li><li>Non Smoking Accommodation</li><li>Playground</li><li>Pool</li><li>Pool – Solar Heated</li></ul>
</section>
<div class="dots" style="position:absolute;left:580px;top:3212px"><i class="on"></i><i></i><i></i></div>

<footer class="footer">
  <div class="fcol" style="left:100px;width:200px">
    <h4>Contact</h4>
    <p>Pinebrook Stays<br><br>12 Fernhill Lane<br>Alder Bay<br>Northshire AB1 2CD<br><br>Phone: 0800 555 0142<br>Bookings: 0800 555 0143<br>hello@pinebrookstays.com</p>
  </div>
  <div class="fcol" style="left:340px;width:200px">
    <h4>Quick Links</h4>
    <ul><li>Available dates</li><li>About our lodges</li><li>Caravans for rent</li><li>Late deals this month</li><li>Guest reviews</li><li>Park facilities</li><li>Local attractions</li><li>Contact us</li></ul>
  </div>
  <div class="fcol" style="left:580px;width:240px">
    <h4>Latest Tweets</h4>
    <p>@pinebrookstays Sunny start to the week on the lake. Only two lodges left for half term, book today. 2 days ago</p><br>
    <p>@pinebrookstays Our new play area is now open for little ones, come and see it this weekend. 5 days ago</p>
  </div>
  <div class="fcol" style="left:860px;width:240px">
    <h4>Contact Us</h4>
    <div class="f-input">Name</div>
    <div class="f-input">Email</div>
    <div class="f-input" style="height:70px">Message</div>
    <span class="f-btn">SUBMIT</span>
  </div>
</footer>
<div class="copyright">Copyright © 2015 Pinebrook Stays – All Rights Reserved</div>

</body>
</html>
```